Visitenkarten-Design für Sonnen-/Fensterschutz
Zielgruppe
KLW GmbH ist eine Firma, die Sonnenschutz und Fensterschutz anbieten.
'Ihr kompetenter Partner in Sachen Sonnenschutz- , Fenster- und Türtechnik. Sie erhalten echtes Handwerk aus dem Mühlviertel zu fairen Preisen.'
Unsere Zielgruppe sind Personen mit Haus, die am Land leben.
Firmenname: KLW GmbH
Slogan: Fenster & Sonnenschutz
Aufgabenstellung
Hier befindet sich das Logodesign: https://dx.qv/t-QwLpo7RbNs
Bitte ein schlichtes Design bereitstellen mit einer Dummy-Person:
Jonas Weidlinger + Telefonnummer + Email
Die finalen Daten bitte erst am Schluss berücksichtigen (für Gewinnerdesign)
Gerne auch hintern + vorne bedruckbar bereitstellen.

```html
<!DOCTYPE html>
<html lang="de">
<head>
<meta charset="utf-8">
<title>KLW GmbH – Visitenkarte</title>
<link rel="stylesheet" href="https://fonts.googleapis.com/css2?family=Montserrat:wght@400;600;700&family=Open+Sans:wght@400;600&family=Orbitron:wght@700&display=swap">
<style>
  :root {
    --stage: #5a5a5a;
    --paper: #ffffff;
    --ink: #4a4a4a;
    --orange: #e8671f;
    --red: #d42a26;
    --brand-start: #e0642a;
    --brand-end: #d42a26;
    --white: #ffffff;
  }
  * { margin: 0; padding: 0; box-sizing: border-box; }
  html, body {
    width: 1200px; height: 1200px; overflow: hidden;
    background: var(--stage);
  }
  .stage { position: relative; width: 1200px; height: 1200px; }

  .card { position: absolute; left: 280px; width: 669px; height: 433px; }

  /* Front */
  .card-front { top: 130px; background: var(--paper); }
  .front-brand {
    position: absolute; left: 360px; top: 62px;
    display: flex; align-items: center; gap: 14px;
    font-family: "Montserrat", sans-serif; font-weight: 700;
    font-size: 44px; color: var(--orange); letter-spacing: 1px;
  }
  .front-brand .mark { width: 34px; height: 34px; background: var(--orange); }

  .contact {
    position: absolute; left: 65px; top: 178px;
    font-family: "Montserrat", sans-serif; font-size: 20px; color: var(--ink);
    line-height: 1.3;
  }
  .contact-company { margin-left: 28px; font-weight: 600; font-size: 18px; color: #777; margin-bottom: 6px; }
  .contact-row { display: flex; align-items: flex-start; gap: 8px; margin-bottom: 11px; }
  .contact-row svg { flex: none; width: 22px; height: 22px; margin-top: 3px; }

  .divider {
    position: absolute; left: 354px; top: 168px;
    width: 2px; height: 171px; background: var(--orange);
  }
  .person {
    position: absolute; left: 380px; width: 240px; top: 228px; text-align: center;
    font-family: "Open Sans", sans-serif; color: var(--ink);
  }
  .person-name { font-size: 26px; font-weight: 400; }
  .person-role { font-size: 19px; font-weight: 600; margin-top: 4px; }

  .front-band {
    position: absolute; left: 0; right: 0; top: 400px; height: 12px;
    background: linear-gradient(90deg, var(--orange), var(--red));
  }

  /* Back */
  .card-back {
    top: 635px;
    background: linear-gradient(90deg, var(--brand-start), var(--brand-end));
  }
  .back-brand {
    position: absolute; left: 0; right: 0; top: 140px;
    display: flex; justify-content: center; align-items: center; gap: 22px;
    font-family: "Montserrat", sans-serif; font-weight: 700;
    font-size: 78px; color: var(--white); letter-spacing: 2px;
  }
  .back-brand .mark { width: 60px; height: 60px; background: var(--white); }
  .back-slogan {
    position: absolute; left: 0; right: 0; top: 314px; text-align: center;
    font-family: "Orbitron", sans-serif; font-weight: 700;
    font-size: 32px; letter-spacing: 2px; color: #f2f2f2;
  }
</style>
</head>
<body>
<main class="stage">
  <section class="card card-front" aria-label="Vorderseite">
    <div class="front-brand"><span class="mark"></span>KLW GmbH</div>

    <div class="contact">
      <p class="contact-company">KLW GmbH</p>
      <div class="contact-row">
        <svg viewBox="0 0 24 24" aria-hidden="true"><path d="M2 3 L22 12 L2 21 L7 12 Z" fill="var(--orange)"/></svg>
        <p>Am Lindenhang 12-14<br>4020 Linz</p>
      </div>
      <div class="contact-row">
        <svg viewBox="0 0 24 24" aria-hidden="true"><path d="M6 2 L10 6 L8 9 C9 12 12 15 15 16 L18 14 L22 18 L19 22 C10 21 3 14 2 5 Z" fill="var(--orange)"/></svg>
        <p>+49 170 555 0182</p>
      </div>
      <div class="contact-row">
        <svg viewBox="0 0 24 24" aria-hidden="true"><rect x="2" y="5" width="20" height="14" rx="1" fill="var(--orange)"/><path d="M2 6 L12 13 L22 6" fill="none" stroke="#fff" stroke-width="1.8"/></svg>
        <p>klwfenster@mailpost.de</p>
      </div>
    </div>

    <div class="divider"></div>

    <div class="person">
      <p class="person-name">Jonas Weidlinger</p>
      <p class="person-role">Geschäftsführer</p>
    </div>

    <div class="front-band"></div>
  </section>

  <section class="card card-back" aria-label="Rückseite">
    <div class="back-brand"><span class="mark"></span>KLW GmbH</div>
    <p class="back-slogan">FENSTER &amp; SONNENSCHUTZ</p>
  </section>
</main>
</body>
</html>
```